Investment firm needs website redesign

we want to change our site with a trendy new design. We are an investment trading firm dealing in currencies etc for retail clients. We are looking for new ideas for our website design which shows class and international reach. We want the inner pages also to be designed especially the look. We do not want the typical designs used by most sites and are looking for something new and interesting. you can review our current site www.trovanique-exchange.com.

Target Market(s)

international

Industry/Entity Type

Forex

Coding

Coded - Design and coding required

Number of Pages Required

5+ page

Font styles to use
Sans Serif

Colors

Designer to choose colors to be used in the design.

Requirements
Must have
• responsive, easy to load
Nice to have
• something trendy yet sophisticated. technology is an important part of our business
Should not have
• do not want the typical designs used by most websites

```html
<!DOCTYPE html>
<html lang="en">
<head>
<meta charset="utf-8">
<title>Trovanique Markets</title>
<link href="https://fonts.googleapis.com/css2?family=Lato:wght@400;700;900&family=Montserrat:wght@600;700&display=swap" rel="stylesheet">
<style>
:root{
  --navy:#1d2b3c;
  --navy-deep:#16212f;
  --gold:#f1ad1d;
  --gold-dark:#d9930f;
  --white:#ffffff;
  --ink:#1a1a1a;
  --muted:#6b7280;
  --line:#d8d8d8;
  --red:#e53935;
  --green:#2e9e41;
  --blue:#2f6db5;
}
*{box-sizing:border-box;margin:0;padding:0}
html,body{width:1200px;height:3429px;overflow:hidden}
body{font-family:"Lato",sans-serif;color:var(--ink);background:#fff;position:relative}
.abs{position:absolute}
h2,h3{font-family:"Montserrat",sans-serif}

.topbar{top:0;left:0;width:1200px;height:46px;background:var(--navy);display:flex;align-items:center;justify-content:space-between;padding:0 98px}
.social{display:flex;gap:14px}
.social span{width:12px;height:12px;border-radius:50%;background:#fff;display:block}
.toplinks{display:flex;gap:30px;color:#fff;font-size:13px}

.header{top:46px;left:0;width:1200px;height:107px;background:#fff;display:flex;align-items:center;justify-content:space-between;padding:0 98px}
.brand{display:flex;align-items:center;gap:8px;font-family:"Montserrat",sans-serif;font-weight:700;font-size:20px;color:var(--navy);white-space:nowrap}
.brand i{width:36px;height:36px;border-radius:50%;background:var(--navy);display:block}
.nav{display:flex;gap:24px;font-family:"Montserrat",sans-serif;font-weight:600;font-size:13px;color:var(--navy);white-space:nowrap}

.updates{top:153px;left:0;width:1200px;height:41px;background:var(--gold);display:flex;align-items:center;justify-content:center;gap:20px;font-size:14px;z-index:2}
.updates b{color:#c0271f;letter-spacing:.5px}
.updates span{color:#1d3a8a;text-decoration:underline}

.hero{top:194px;left:0;width:1200px;height:569px;background:linear-gradient(100deg,#6d6f66 0%,#3d4a45 35%,#24313a 60%,#182530 100%)}
.hero-text{top:335px;left:100px;color:#fff}
.hero-text h1{font-family:"Montserrat",sans-serif;font-size:78px;line-height:90px;font-weight:700;letter-spacing:1px}
.hero-text p{font-weight:700;font-size:19px;line-height:30px;margin-top:14px;width:580px}
.btn{display:inline-flex;align-items:center;gap:10px;background:var(--gold);color:#fff;font-family:"Montserrat",sans-serif;font-weight:700;font-size:15px;border-radius:26px;padding:0 32px;height:50px;white-space:nowrap}
.hero-text .btn{margin-top:30px}
.arrow-l,.arrow-r{top:470px;color:#fff;font-size:26px}

.ticker{top:763px;left:0;width:1200px;height:46px;background:#fff;display:flex;align-items:center;justify-content:center;gap:52px;font-size:12px;color:var(--blue);box-shadow:0 3px 6px rgba(0,0,0,.12)}
.up{color:var(--green)}.dn{color:var(--red)}

.products{top:809px;left:0;width:1200px;height:928px;background:linear-gradient(180deg,#fff 0%,#f3f4f6 100%)}
.ghost{left:0;width:1200px;text-align:center;font-family:"Montserrat",sans-serif;font-weight:700;font-size:74px;color:rgba(0,0,0,.06);white-space:nowrap}
.sec-title{left:0;width:1200px;text-align:center;font-size:34px;font-weight:700;color:var(--ink)}
.lead{left:280px;width:640px;text-align:center;font-size:14px;line-height:24px;color:var(--muted)}
.card{width:307px;height:215px;background:rgba(255,255,255,.9);border:1px solid var(--line);text-align:center;padding:30px 24px 0}
.card svg{display:block;margin:0 auto}
.card h3{font-size:17px;margin:14px 0 10px}
.card p{font-size:13px;line-height:22px;color:var(--muted)}

.trade-photo{top:1737px;left:0;width:583px;height:412px;background:linear-gradient(120deg,#e7ecef,#b7c2cb 50%,#34404f)}
.trade-panel{top:1737px;left:583px;width:617px;height:412px;background:linear-gradient(180deg,var(--gold-dark),var(--gold));padding:60px 40px 60px 72px;color:#fff}
.trade-panel h2{font-size:30px;line-height:48px;white-space:nowrap}
.trade-panel p{font-size:14px;line-height:24px;margin-top:20px;width:470px}
.btn-outline{display:inline-block;margin-top:30px;border:2px solid #fff;border-radius:24px;padding:10px 30px;font-family:"Montserrat",sans-serif;font-weight:700;font-size:14px}

.contract{top:2149px;left:0;width:1200px;height:503px;background:linear-gradient(180deg,#fafafa,#eef0f2)}
.contract h2{top:92px;left:98px;font-size:34px;white-space:nowrap}
.contract .body{top:164px;left:98px;width:480px;font-size:13px;line-height:23px;color:#444}
.contract .btn{top:356px;left:98px;height:44px;font-size:14px}
.video{top:105px;left:638px;width:461px;height:292px;border:4px solid #fff;box-shadow:0 2px 10px rgba(0,0,0,.25);background:linear-gradient(135deg,#0d2a58,#143e7a 50%,#0a1c3a)}
.play{top:120px;left:205px}
.divider{top:503px;left:98px;width:1004px;height:1px;background:var(--line)}

.partners{top:2652px;left:0;width:1200px;height:422px;background:#f7f8f9}
.logo-box{top:237px;width:188px;height:82px;background:#fff;border:1px solid var(--line);display:flex;align-items:center;justify-content:center}
.logo-box span{width:80px;height:40px;border-radius:6px;background:#cfd6de}

.foot-photo{top:3074px;left:0;width:400px;height:355px;background:linear-gradient(180deg,#8fbbe3,#2d63a6 60%,#16325e)}
.foot-mid{top:3074px;left:400px;width:400px;height:355px;background:var(--navy-deep);color:#fff;text-align:center}
.foot-mid h3{font-size:15px;margin-top:58px}
.email{margin:18px auto 0;width:284px;height:38px;border:1px solid #fff;font-size:12px;text-align:left;padding:11px 12px}
.subscribe{margin:12px auto 0;width:132px;height:38px;background:var(--gold);font-weight:700;font-size:14px;line-height:38px}
.contact-row{display:flex;justify-content:center;align-items:center;gap:12px;font-size:13px;margin-top:12px}
.copy{font-size:12px;margin-top:22px}
.map{top:3074px;left:800px;width:400px;height:355px;background:linear-gradient(160deg,#eef0e8,#e3e6dc)}
.totop{top:3049px;left:575px;width:50px;height:50px;border-radius:50%;background:#fff;box-shadow:0 1px 6px rgba(0,0,0,.25)}
</style>
</head>
<body>

<div class="abs topbar">
  <div class="social"><span></span><span></span><span></span><span></span><span></span><span></span><span></span></div>
  <div class="toplinks"><span>Home</span><span>Downloads</span><span>Live Chat Offline</span><span>Disclosure</span><span>Contact</span></div>
</div>

<header class="abs header">
  <div class="brand"><i></i>TROVANIQUE</div>
  <nav class="nav"><span>ABOUT US</span><span>PRODUCTS &amp; SERVICES</span><span>OPEN ACCOUNT</span><span>TRADING PLATFORMS</span><span>TRADING INFO</span><span>MORE ▾</span></nav>
</header>

<div class="abs updates"><b>LATEST UPDATES:</b><span>› Forex – Forex – China Revives Global Yuan Push as Capital Outflow Worries Fade</span></div>

<section class="abs hero" role="img" aria-label="Hands typing on a laptop with a rising market chart and price figures overlaid"></section>
<div class="abs hero-text">
  <h1>TROVANIQUE</h1>
  <p>We offers the White Label Program to Individuals &amp; Institutions that want to establish a brand name in the global markets.</p>
  <span class="btn">READ MORE ➔</span>
</div>
<span class="abs arrow-l" style="left:34px">‹</span>
<span class="abs arrow-r" style="left:1152px">›</span>

<div class="abs ticker">
  <span>GBP/MYR = <b class="up">5.28644▴</b></span>
  <span>GBP/NAD = <b class="dn">16.74624▾</b></span>
  <span>GBP/NGN = <b class="up">480.28034▴</b></span>
  <span>GBP/NIO = <b class="dn">42.16891▾</b></span>
  <span>GBP/NOK = <b class="up">10.81445▴</b></span>
  <span>GBP/NPR = <b class="dn">143.20868▾</b></span>
</div>

<section class="abs products">
  <div class="abs ghost" style="top:70px">PRODUCTS &amp; SERVICES</div>
  <h2 class="abs sec-title" style="top:94px">PRODUCTS &amp; SERVICES</h2>
  <p class="abs lead" style="top:158px">At vero eos et accusamus et iusto odio dignissimos ducimus praesentium voluptatum deleniti atque corrupti quos dolores et quas molestias excepturi sint occaecati cupiditate non provident similique</p>

  <div class="abs card" style="top:245px;left:98px">
    <svg width="70" height="60" viewBox="0 0 70 60"><circle cx="26" cy="24" r="16" fill="none" stroke="#1d2b3c" stroke-width="3"/><path d="M16 28l6-6 5 4 8-9" stroke="#f1ad1d" stroke-width="3" fill="none"/><rect x="44" y="40" width="6" height="14" fill="#f1ad1d"/><rect x="54" y="32" width="6" height="22" fill="#f1ad1d"/><rect x="22" y="40" width="8" height="14" fill="#1d2b3c"/></svg>
    <h3>CFDS</h3><p>CFD's are a synthetic equity product, which mirror the economic benefits</p>
  </div>
  <div class="abs card" style="top:245px;left:446px">
    <svg width="90" height="60" viewBox="0 0 90 60"><rect x="8" y="10" width="64" height="36" fill="#f1ad1d" stroke="#1d2b3c" stroke-width="3"/><rect x="18" y="18" width="64" height="36" fill="#fff" stroke="#1d2b3c" stroke-width="3"/><circle cx="50" cy="36" r="10" fill="#f1ad1d"/></svg>
    <h3>CURRENCIES</h3><p>Trovanique's offers 24 hour trading coverage of all major pairs with services</p>
  </div>
  <div class="abs card" style="top:245px;left:793px">
    <svg width="70" height="60" viewBox="0 0 70 60"><rect x="14" y="38" width="8" height="16" fill="#1d2b3c"/><rect x="28" y="28" width="8" height="26" fill="#1d2b3c"/><rect x="42" y="18" width="8" height="36" fill="#1d2b3c"/><circle cx="52" cy="8" r="6" fill="#f1ad1d"/><path d="M10 56h52" stroke="#1d2b3c" stroke-width="3"/></svg>
    <h3>FUTURES</h3><p>A futures contract is a standardized agreement, made on a recognized</p>
  </div>
  <div class="abs card" style="top:501px;left:98px">
    <svg width="90" height="60" viewBox="0 0 90 60"><rect x="6" y="4" width="78" height="44" fill="#fff" stroke="#1d2b3c" stroke-width="3"/><path d="M14 38l14-12 12 8 16-18 18 10" stroke="#f1ad1d" stroke-width="3" fill="none"/><path d="M36 56h18" stroke="#1d2b3c" stroke-width="4"/></svg>
    <h3>STOCKS</h3><p>Trovanique provides clients with 24-hour execution on global exchanges.</p>
  </div>
  <div class="abs card" style="top:501px;left:446px">
    <svg width="70" height="60" viewBox="0 0 70 60"><rect x="18" y="4" width="38" height="50" fill="#fff" stroke="#1d2b3c" stroke-width="3"/><path d="M26 16h22M26 24h22M26 32h14" stroke="#1d2b3c" stroke-width="2"/><circle cx="22" cy="42" r="10" fill="#f1ad1d"/></svg>
    <h3>BONDS</h3><p>A bond is a debt security, wherein an authorized issuer owes the holders</p>
  </div>
  <div class="abs card" style="top:501px;left:793px">
    <svg width="70" height="60" viewBox="0 0 70 60"><circle cx="24" cy="22" r="12" fill="#f1ad1d" stroke="#1d2b3c" stroke-width="2"/><circle cx="46" cy="24" r="12" fill="#fff" stroke="#1d2b3c" stroke-width="2"/><circle cx="34" cy="42" r="12" fill="#f1ad1d" stroke="#1d2b3c" stroke-width="2"/></svg>
    <h3>CRYPTO CURRENCIES</h3><p>Cryptocurrencies also known as digital currencies are fastest growing</p>
  </div>

  <span class="abs btn" style="top:776px;left:467px;height:50px;font-size:14px">VIEW ALL SERVICES ➔</span>
</section>

<div class="abs trade-photo" role="img" aria-label="Team of traders in an office gathered around a computer showing market charts"></div>
<div class="abs trade-panel">
  <h2>START YOUR TRADING WITH<br>TROVANIQUE MARKETS</h2>
  <p>Nemo enim ipsam voluptatem quia voluptas sit aspernatur aut odit aut fugit, sed quia consequuntur magni dolores eos qui ratione voluptatem sequi nesciunt. Neque porro quisquam est, qui dolorem</p>
  <span class="btn-outline">JOIN US TODAY</span>
</div>

<section class="abs contract">
  <h2 class="abs">CONTRACT SPECIFICATIONS</h2>
  <div class="abs body">
    <p>At vero eos et accusamus et iusto odio dignissimos ducimus blanditiis praesentium voluptatum deleniti atque.</p>
    <p style="margin-top:16px">Occaecati cupiditate non provident, similique sunt in culpa qui officia deserunt mollitia animi, id est laborum et dolorum fuga. Et harum quidem rerum facilis est et expedita distinctio. Nam libero tempore, cum soluta nobis est eligendi optio cumque nihil impedit quo minus beatae sequi vero sed possimus.</p>
  </div>
  <span class="abs btn">READ MORE ➔</span>
  <div class="abs video" role="img" aria-label="Video thumbnail listing digital currency names over a rising market chart">
    <svg class="abs play" width="52" height="52" viewBox="0 0 52 52"><circle cx="26" cy="26" r="26" fill="#e02020"/><path d="M20 15l18 11-18 11z" fill="#fff"/></svg>
  </div>
  <div class="abs divider"></div>
</section>

<section class="abs partners">
  <div class="abs ghost" style="top:86px">OUR PARTNERS</div>
  <h2 class="abs sec-title" style="top:112px">OUR PARTNERS</h2>
  <p class="abs lead" style="top:156px;left:230px;width:740px;font-size:15px">At vero eos et accusamus et iusto odio dignissimos ducimus qui blanditiis praesentium voluptatum deleniti atque corrupti quos dolores et quas molestias excepturi cupiditate non provident.</p>
  <span class="abs" style="top:262px;left:40px;font-size:26px;color:#555">‹</span>
  <div class="abs logo-box" style="left:98px"><span></span></div>
  <div class="abs logo-box" style="left:302px"><span></span></div>
  <div class="abs logo-box" style="left:506px"><span style="background:#111"></span></div>
  <div class="abs logo-box" style="left:710px"><span></span></div>
  <div class="abs logo-box" style="left:914px"><span style="background:#111"></span></div>
  <span class="abs" style="top:262px;left:1144px;font-size:26px;color:#555">›</span>
</section>

<div class="abs foot-photo" role="img" aria-label="Modern glass office tower against a blue sky"></div>
<footer class="abs foot-mid">
  <h3>NEWSLETTER SUBSCRIPTION</h3>
  <div class="email">Email</div>
  <div class="subscribe">SUBSCRIBE</div>
  <h3 style="margin-top:26px">CONTACT US</h3>
  <div class="contact-row"><svg width="14" height="14" viewBox="0 0 24 24"><path d="M6 2l4 4-2 3c1 3 4 6 7 7l3-2 4 4-3 4C10 22 2 14 2 5z" fill="#fff"/></svg>(+1) 555 014 2290</div>
  <div class="contact-row"><svg width="16" height="12" viewBox="0 0 16 12"><rect width="16" height="12" fill="#fff"/><path d="M0 0l8 6 8-6" stroke="#16212f" fill="none"/></svg>info@trovanique-exchange.com</div>
  <p class="copy">© Copyright 2018 Trovanique Markets. All Rights Reserved.</p>
</footer>
<div class="abs map" role="img" aria-label="Street map showing the office location with a red pin"></div>
<div class="abs totop"><svg width="50" height="50" viewBox="0 0 50 50"><path d="M17 26l8-8 8 8M17 33l8-8 8 8" stroke="#1d2b3c" stroke-width="2.5" fill="none"/></svg></div>

</body>
</html>
```